Road Construction Company needs business cards

We would like a new business card designed for our business.

We're a road construction company based in Qld, Australia.

Can the business card please have the following information on it.

Name: Warren Halbeck
Position: General Manager
Phone: 0472 915 348
Email: Warren.halbeck@tovrin.com.au
Address: 87 Marrow Ave, Pendlebay, QLD, 4023
Website: www.tovrin.com.au

Visually we'd like the card to be professional and simple.

Attached is our logo.

Our website is www.tovrin.com.au

Target Market(s)

Men aged 25-60

Contact Information for Business Card

As listed in project description

Font styles to use
Serif

Requirements
Must have
• Large logo on back of card

```html
<!DOCTYPE html>
<html lang="en">
<head>
<meta charset="utf-8">
<title>Tovrin Business Card</title>
<link rel="stylesheet" href="https://fonts.googleapis.com/css2?family=Barlow:wght@400;500;700&family=Barlow+Semi+Condensed:wght@700&display=swap">
<style>
  :root {
    --brand-blue: #0a53a1;
    --brand-sky: #2ea5da;
    --brand-deep: #17255f;
    --brand-light: #66b5e4;
    --ink: #4b4b4b;
    --paper: #ffffff;
    --stage: #e6e7e9;
  }
  * { box-sizing: border-box; margin: 0; padding: 0; }
  html, body { width: 1200px; height: 588px; overflow: hidden; }
  body {
    background: var(--stage);
    font-family: "Barlow", sans-serif;
    position: relative;
  }
  .card {
    position: absolute;
    width: 487px;
    height: 287px;
    overflow: hidden;
  }
  .card-front { left: 87px; top: 141px; background: var(--paper); }
  .card-back { left: 622px; top: 143px; background: var(--brand-blue); }

  .front-panel {
    position: absolute;
    top: 0;
    right: 0;
    width: 118px;
    height: 100%;
    background: var(--brand-blue);
  }
  .front-stripe {
    position: absolute;
    top: 0;
    right: 126px;
    width: 8px;
    height: 100%;
    background: var(--brand-sky);
  }
  .back-panel {
    position: absolute;
    top: 0;
    left: 0;
    width: 190px;
    height: 100%;
    background: linear-gradient(160deg, var(--brand-deep) 0%, #1a5aa8 50%, var(--brand-light) 100%);
  }

  .wordmark {
    position: absolute;
    font-family: "Barlow", sans-serif;
    font-weight: 700;
    line-height: 1;
  }
  .card-front .wordmark {
    left: 26px;
    top: 28px;
    font-size: 40px;
    letter-spacing: 4px;
    color: var(--brand-blue);
  }
  .card-back .wordmark {
    right: 31px;
    top: 116px;
    font-size: 48px;
    letter-spacing: 5px;
    color: var(--paper);
  }
  .accent-bar {
    position: absolute;
    left: 0;
    top: 94px;
    width: 12px;
    height: 35px;
    background: var(--brand-sky);
  }
  .person-name {
    position: absolute;
    left: 25px;
    top: 91px;
    font-family: "Barlow Semi Condensed", sans-serif;
    font-weight: 700;
    font-size: 19px;
    color: var(--brand-blue);
    text-transform: uppercase;
  }
  .person-role {
    position: absolute;
    left: 25px;
    top: 114px;
    font-size: 13.5px;
    color: var(--brand-sky);
  }
  .address {
    position: absolute;
    left: 25px;
    top: 151px;
    font-size: 13px;
    line-height: 19px;
    color: var(--ink);
    font-style: normal;
  }
  .contacts {
    position: absolute;
    left: 25px;
    top: 206px;
    list-style: none;
    font-size: 13px;
    line-height: 18.6px;
    color: var(--ink);
  }
  .contacts li { display: flex; align-items: center; gap: 5px; }
  .contacts svg { width: 11px; height: 11px; fill: var(--brand-blue); flex: none; }
  .web-domain { color: var(--brand-blue); font-weight: 500; }
</style>
</head>
<body>
  <section class="card card-front" aria-label="Card front">
    <div class="front-stripe" role="img" aria-label="Decorative brand stripe"></div>
    <div class="front-panel" role="img" aria-label="Decorative brand panel"></div>
    <div class="wordmark">TOVRIN</div>
    <span class="accent-bar"></span>
    <h1 class="person-name">Warren Halbeck</h1>
    <p class="person-role">General Manager</p>
    <address class="address">87 Marrow Ave<br>Pendlebay, QLD, 4023</address>
    <ul class="contacts">
      <li>
        <svg viewBox="0 0 24 24" aria-hidden="true"><path d="M6.6 10.8a15.1 15.1 0 0 0 6.6 6.6l2.2-2.2a1 1 0 0 1 1-.25 11.4 11.4 0 0 0 3.6.57 1 1 0 0 1 1 1V20a1 1 0 0 1-1 1A17 17 0 0 1 3 4a1 1 0 0 1 1-1h3.5a1 1 0 0 1 1 1c0 1.25.2 2.45.57 3.57a1 1 0 0 1-.25 1z"/></svg>
        0472 915 348
      </li>
      <li>
        <svg viewBox="0 0 24 24" aria-hidden="true"><path d="M2 5h20v2l-10 6L2 7z M2 9l10 6 10-6v10H2z"/></svg>
        Warren.halbeck@tovrin.com.au
      </li>
      <li>
        <svg viewBox="0 0 24 24" aria-hidden="true"><path d="M12 2a10 10 0 1 0 0 20 10 10 0 0 0 0-20zm-1 17.9A8 8 0 0 1 4.1 11H7v2l3 3v3.9zm6.9-2.5A2 2 0 0 0 16 16h-1v-3H9v-2h2V8h2V5.5a8 8 0 0 1 4.9 11.9z"/></svg>
        <span>www.<span class="web-domain">tovrin</span>.com.au</span>
      </li>
    </ul>
  </section>

  <section class="card card-back" aria-label="Card back">
    <div class="back-panel" role="img" aria-label="Decorative brand gradient panel"></div>
    <div class="wordmark">TOVRIN</div>
  </section>
</body>
</html>
```